Need help in designing new business card utilizing our new logo.

BuildMark Solutions works with Construction Business Owners, Managers & IT Professionals to strengthen software usage and increase user productivity.

Our Construction Accounting and Mobile Field Management Software Clients engage with us in the following areas:

New Software Implementations
Software Re-Implementations
Redesigning Software Usage at the User Level
Project Coordination & Management
Continued Software Support

Old tag line:
Planning Ahead - Delivering Results

www.buildmark-solutions.example

Ridge 4 is a product, but not needed for a new business card.

```html
<!DOCTYPE html>
<html lang="en">
<head>
<meta charset="utf-8">
<title>BuildMark Solutions – Business Card</title>
<link rel="stylesheet" href="https://fonts.googleapis.com/css2?family=Roboto:wght@400;500;700&family=Roboto+Condensed:wght@700&display=swap">
<style>
  :root {
    --backdrop: #b9b9b9;
    --card-light: #f7f7f7;
    --card-shade: #e2e2e2;
    --brand-blue: #0b129a;
    --band-text: #f2f3ff;
    --body-text: #3a3a3a;
    --rule-grey: #9a9a9a;
  }
  * { box-sizing: border-box; margin: 0; padding: 0; }
  html, body {
    width: 1200px; height: 576px; overflow: hidden;
    background: var(--backdrop);
    font-family: "Roboto", Arial, sans-serif;
  }
  .canvas { position: relative; width: 1200px; height: 576px; }
  .card {
    position: absolute; top: 138px; width: 484px; height: 294px;
    border-radius: 14px; overflow: hidden;
    background: linear-gradient(135deg, var(--card-light) 0%, #ececec 55%, var(--card-shade) 100%);
  }
  .card--front { left: 82px; }
  .card--back { left: 602px; }

  .wordmark { display: flex; align-items: center; gap: 12px; color: var(--brand-blue); font-weight: 700; white-space: nowrap; }
  .wordmark__square { background: var(--brand-blue); flex: none; }

  .card--front .wordmark { position: absolute; top: 56px; left: 0; width: 100%; justify-content: center; font-size: 32px; letter-spacing: 0.5px; }
  .card--front .wordmark__square { width: 46px; height: 46px; }

  .services-band {
    position: absolute; top: 167px; left: 0; width: 100%; height: 80px;
    background: var(--brand-blue); color: var(--band-text);
    display: flex; flex-direction: column; justify-content: center; align-items: center;
    font-size: 13px; line-height: 18.5px; text-align: center; white-space: nowrap;
  }
  .services-band .sep { margin: 0 9px; }

  .front-web {
    position: absolute; top: 262px; left: 0; width: 100%;
    display: flex; justify-content: center; align-items: center; gap: 14px;
    color: var(--brand-blue); font-size: 12px; white-space: nowrap;
  }
  .front-web__rule { width: 42px; height: 1px; background: linear-gradient(90deg, transparent, var(--rule-grey), transparent); }

  .card--back .wordmark { position: absolute; top: 108px; left: 26px; font-size: 22px; line-height: 24px; }
  .card--back .wordmark__square { width: 38px; height: 38px; }

  .contact { position: absolute; top: 52px; left: 260px; color: var(--body-text); white-space: nowrap; }
  .contact__name { font-family: "Roboto Condensed", "Arial Narrow", sans-serif; font-weight: 700; font-size: 21px; color: var(--brand-blue); }
  .contact__role { font-size: 12px; margin-top: 3px; }
  .contact__address { font-size: 12px; line-height: 17px; margin-top: 14px; }
  .contact__list { list-style: none; margin-top: 7px; font-size: 12px; line-height: 17px; }
  .contact__list li { display: flex; align-items: center; gap: 9px; }
  .contact__list svg { width: 11px; height: 11px; fill: var(--brand-blue); flex: none; }

  .tagline-band {
    position: absolute; left: 0; bottom: 0; width: 100%; height: 29px;
    background: var(--brand-blue); color: var(--band-text);
    display: flex; align-items: center; justify-content: center; font-size: 12px;
  }
</style>
</head>
<body>
<main class="canvas">
  <section class="card card--front" aria-label="Card front">
    <div class="wordmark"><span class="wordmark__square"></span><span>BuildMark Solutions</span></div>
    <div class="services-band">
      <p>New Software Implementations<span class="sep">|</span>Software Re-Implementations</p>
      <p>Redesigning Software Usage at the User Level</p>
      <p>Project Coordination &amp; Management<span class="sep">|</span>Continued Software Support</p>
    </div>
    <div class="front-web"><span class="front-web__rule"></span><span>www.buildmark-solutions.example</span><span class="front-web__rule"></span></div>
  </section>

  <section class="card card--back" aria-label="Card back">
    <div class="wordmark"><span class="wordmark__square"></span><span>BuildMark<br>Solutions</span></div>
    <div class="contact">
      <h1 class="contact__name">Dana R. Whitfield</h1>
      <p class="contact__role">Owner</p>
      <p class="contact__address">14B Harbor Lane - Suite 310<br>Millbrook, NY 12000</p>
      <ul class="contact__list">
        <li><svg viewBox="0 0 12 12"><path d="M3 0h6a1 1 0 0 1 1 1v10a1 1 0 0 1-1 1H3a1 1 0 0 1-1-1V1a1 1 0 0 1 1-1zm0 1.5v8h6v-8z"/></svg>555-014-2267</li>
        <li><svg viewBox="0 0 12 12"><path d="M0 4c0-2 3-3 6-3s6 1 6 3v1H9V3.6H3V5H0zM2 6h8l1 5H1z"/></svg>800-555-0142 ext. 100</li>
        <li><svg viewBox="0 0 12 12"><path d="M0 2h12v8H0zm1 1v.3l5 3.5 5-3.5V3z"/></svg>dana@buildmark-solutions.example</li>
        <li><svg viewBox="0 0 12 12"><path d="M6 0a6 6 0 1 1 0 12A6 6 0 0 1 6 0zm0 1C5 2 4.5 4 4.5 6S5 10 6 11c1-1 1.5-3 1.5-5S7 2 6 1zM1.2 5.5h9.6v1H1.2z"/></svg>www.buildmark-solutions.example</li>
      </ul>
    </div>
    <div class="tagline-band">Planning Ahead - Delivering Results</div>
  </section>
</main>
</body>
</html>
```